Catalogue Design Project

We require a new 2013 catalogue cover designed ( front & back with a one inch wide spine) for our business, Brevik Office Supplies. We have been established for 36 years and we supply all sorts of companies across the UK with a Variety of Office Stationery, Computer Products, Print, Furniture, Catering and Cleaning products within the UK - you can browse our catalogue on our website www.brevik-demo.co.uk - using test as both user id and password.
We are serious about customer service; ensure we do the very best for our clients with the best prices. For us it’s all about the image we portray to our clients, we don’t want the cover to look like it’s the cover of a Yacht catalogue, nor do we want it to look like a trashy magazine.
The main priority of this design is that the Catalogue looks professional and appealing. Good use of colour, possibly incorporating elements of what we do would be of advantage.
(Please visit our website www.brevik-demo.co.uk for details).
The Catalogue is to be A4 in size, MUST have our company logo in on the front, which we will supply, but for the start obtainable from our site)
The Catalogue covers will have insides both front and back that we will be printing on. Your design and use of colours should be able to flow onto these pages so as we can print on a continuation of your design.
**UPDATE - Please note the content is already designed, this is for the front/back cover and inside covers**
There will be a few edits after we make a choice...
if you need anything from us then please email us on jlowe@brevik-demo.co.uk
Best of luck
Reason: Deaedline Extended to give you all a chance to get your designs in!!
Reason: Having some great creative ideas in, so herew is a chance for one last push before we make our decision.
PROJECT NOW GUARANTEED.!!
Due to the High Quality of designs being submitted - we are now happy to commit to one of you! Keep the designs coming!
Good Luck!
The Buyers of our products are corporate companies
Printing

```html
<!DOCTYPE html>
<html lang="en">
<head>
<meta charset="utf-8">
<title>Brevik Office Supplies – 2013 Catalogue Covers</title>
<link href="https://fonts.googleapis.com/css2?family=Roboto+Condensed:wght@400;700&display=swap" rel="stylesheet">
<style>
  :root {
    --backdrop: #dcdcdc;
    --yellow: #f4d726;
    --yellow-deep: #eccf20;
    --paper: #ffffff;
    --fold-grey: #cfcfcf;
    --ink-grey: #8c8c8c;
    --caption: #555555;
    --tape-red: #c8321e;
    --tape-orange: #e8762a;
    --tape-clear: #f1ede4;
  }
  * { box-sizing: border-box; margin: 0; padding: 0; }
  html, body {
    width: 1200px; height: 900px; overflow: hidden;
    background: var(--backdrop);
    font-family: "Roboto Condensed", Arial, sans-serif;
  }
  .spread {
    position: absolute; left: 80px; width: 1040px; height: 380px;
    box-shadow: 0 4px 14px rgba(0,0,0,0.18);
  }
  .inside-spread { top: 50px; background: var(--paper); }
  .cover-spread { top: 470px; }
  .spread > svg { position: absolute; inset: 0; display: block; }

  .section-title {
    position: absolute; top: 34px;
    color: var(--paper); font-weight: 700; font-size: 17px; line-height: 1.05;
  }
  .section-title.left-page { left: 440px; }
  .section-title.right-page { left: 530px; }

  .product-grid {
    position: absolute; top: 40px;
    display: grid; grid-template-columns: repeat(4, 72px);
    grid-auto-rows: 70px; column-gap: 6px; row-gap: 2px;
  }
  .product-grid.left-page { left: 40px; }
  .product-grid.right-page { left: 700px; }
  .product { display: flex; flex-direction: column; gap: 3px; }
  .product-shot {
    width: 66px; height: 46px; border: 1px solid #e4e4e4;
    background:
      radial-gradient(circle at 68% 62%, var(--tape-clear) 0 30%, transparent 31%),
      linear-gradient(135deg, var(--tape-red) 0 45%, var(--tape-orange) 46% 58%, #f7f7f7 59%);
  }
  .product figcaption {
    font-size: 8px; color: var(--caption); line-height: 1.1;
    white-space: nowrap; overflow: hidden; text-overflow: ellipsis; max-width: 72px;
  }

  .page-brand {
    position: absolute; top: 346px; color: var(--ink-grey);
    font-size: 14px; font-weight: 400; letter-spacing: 0.3px; white-space: nowrap;
  }
  .page-brand.left-page { left: 240px; }
  .page-brand.right-page { left: 560px; }
  .edition-tag {
    position: absolute; top: 330px; color: var(--fold-grey);
    font-size: 13px; font-weight: 700; letter-spacing: 1px;
    transform: rotate(-90deg); transform-origin: left top; white-space: nowrap;
  }
  .edition-tag.left-page { left: 356px; }
  .edition-tag.right-page { left: 604px; }

  .cover-text { fill: var(--paper); font-family: "Roboto Condensed", Arial, sans-serif; }
  .cover-text .label { font-size: 15px; font-weight: 400; }
  .cover-text .year { font-size: 34px; font-weight: 700; }
  .cover-brand { fill: var(--paper); font-size: 20px; font-weight: 400; font-family: "Roboto Condensed", Arial, sans-serif; }
</style>
</head>
<body>

<section class="spread inside-spread" aria-label="Inside covers">
  <svg width="1040" height="380" viewBox="0 0 1040 380">
    <line x1="520" y1="0" x2="520" y2="380" stroke="#e2e2e2" stroke-width="2"/>
    <path d="M410,0 Q430,230 512,380 L520,380 L520,0 Z" fill="var(--fold-grey)"/>
    <path d="M418,0 Q440,220 520,372 L520,0 Z" fill="var(--yellow)"/>
    <path d="M630,0 Q610,230 528,380 L520,380 L520,0 Z" fill="var(--fold-grey)"/>
    <path d="M622,0 Q600,220 520,372 L520,0 Z" fill="var(--yellow)"/>
  </svg>

  <h2 class="section-title left-page">Adhesives<br>&amp;Tapes</h2>
  <h2 class="section-title right-page">Adhesives<br>&amp;Tapes</h2>

  <div class="product-grid left-page">
    <figure class="product"><div class="product-shot" role="img" aria-label="Boxed roll of adhesive tape"></div><figcaption>Clear Tape 19mm</figcaption></figure>
    <figure class="product"><div class="product-shot" role="img" aria-label="Boxed roll of adhesive tape"></div><figcaption>Clear Tape 25mm</figcaption></figure>
    <figure class="product"><div class="product-shot" role="img" aria-label="Boxed roll of adhesive tape"></div><figcaption>Matt Tape 19mm</figcaption></figure>
    <figure class="product"><div class="product-shot" role="img" aria-label="Boxed roll of adhesive tape"></div><figcaption>Matt Tape 25mm</figcaption></figure>
    <figure class="product"><div class="product-shot" role="img" aria-label="Boxed roll of adhesive tape"></div><figcaption>Office Tape Roll</figcaption></figure>
    <figure class="product"><div class="product-shot" role="img" aria-label="Boxed roll of adhesive tape"></div><figcaption>Tape Refill Pack</figcaption></figure>
    <figure class="product"><div class="product-shot" role="img" aria-label="Boxed roll of adhesive tape"></div><figcaption>Invisible Tape 19mm</figcaption></figure>
    <figure class="product"><div class="product-shot" role="img" aria-label="Boxed roll of adhesive tape"></div><figcaption>Invisible Tape 12mm</figcaption></figure>
    <figure class="product"><div class="product-shot" role="img" aria-label="Boxed roll of adhesive tape"></div><figcaption>Double Sided Tape</figcaption></figure>
    <figure class="product"><div class="product-shot" role="img" aria-label="Boxed roll of adhesive tape"></div><figcaption>Mounting Tape Roll</figcaption></figure>
    <figure class="product"><div class="product-shot" role="img" aria-label="Boxed roll of adhesive tape"></div><figcaption>Removable Tape</figcaption></figure>
    <figure class="product"><div class="product-shot" role="img" aria-label="Boxed roll of adhesive tape"></div><figcaption>Gift Tape Roll</figcaption></figure>
    <figure class="product"><div class="product-shot" role="img" aria-label="Boxed roll of adhesive tape"></div><figcaption>Dispenser Red</figcaption></figure>
    <figure class="product"><div class="product-shot" role="img" aria-label="Boxed roll of adhesive tape"></div><figcaption>Dispenser Black</figcaption></figure>
    <figure class="product"><div class="product-shot" role="img" aria-label="Boxed roll of adhesive tape"></div><figcaption>Handheld Dispenser</figcaption></figure>
    <figure class="product"><div class="product-shot" role="img" aria-label="Boxed roll of adhesive tape"></div><figcaption>Tape Value Pack</figcaption></figure>
  </div>

  <div class="product-grid right-page">
    <figure class="product"><div class="product-shot" role="img" aria-label="Boxed roll of adhesive tape"></div><figcaption>Packing Tape Brown</figcaption></figure>
    <figure class="product"><div class="product-shot" role="img" aria-label="Boxed roll of adhesive tape"></div><figcaption>Packing Tape Clear</figcaption></figure>
    <figure class="product"><div class="product-shot" role="img" aria-label="Boxed roll of adhesive tape"></div><figcaption>Masking Tape 25mm</figcaption></figure>
    <figure class="product"><div class="product-shot" role="img" aria-label="Boxed roll of adhesive tape"></div><figcaption>Masking Tape 50mm</figcaption></figure>
    <figure class="product"><div class="product-shot" role="img" aria-label="Boxed roll of adhesive tape"></div><figcaption>Duct Tape Silver</figcaption></figure>
    <figure class="product"><div class="product-shot" role="img" aria-label="Boxed roll of adhesive tape"></div><figcaption>Duct Tape Black</figcaption></figure>
    <figure class="product"><div class="product-shot" role="img" aria-label="Boxed roll of adhesive tape"></div><figcaption>Hazard Tape Yellow</figcaption></figure>
    <figure class="product"><div class="product-shot" role="img" aria-label="Boxed roll of adhesive tape"></div><figcaption>Floor Tape Red</figcaption></figure>
    <figure class="product"><div class="product-shot" role="img" aria-label="Boxed roll of adhesive tape"></div><figcaption>Glue Stick 40g</figcaption></figure>
    <figure class="product"><div class="product-shot" role="img" aria-label="Boxed roll of adhesive tape"></div><figcaption>Glue Stick 20g</figcaption></figure>
    <figure class="product"><div class="product-shot" role="img" aria-label="Boxed roll of adhesive tape"></div><figcaption>Liquid Glue Pen</figcaption></figure>
    <figure class="product"><div class="product-shot" role="img" aria-label="Boxed roll of adhesive tape"></div><figcaption>Adhesive Putty</figcaption></figure>
    <figure class="product"><div class="product-shot" role="img" aria-label="Boxed roll of adhesive tape"></div><figcaption>Spray Adhesive</figcaption></figure>
    <figure class="product"><div class="product-shot" role="img" aria-label="Boxed roll of adhesive tape"></div><figcaption>Glue Dots Roll</figcaption></figure>
    <figure class="product"><div class="product-shot" role="img" aria-label="Boxed roll of adhesive tape"></div><figcaption>Correction Roller</figcaption></figure>
    <figure class="product"><div class="product-shot" role="img" aria-label="Boxed roll of adhesive tape"></div><figcaption>Tape Gun Heavy</figcaption></figure>
  </div>

  <p class="edition-tag left-page">2013 Catalogue</p>
  <p class="page-brand left-page">Brevik Office Supplies</p>
  <p class="edition-tag right-page">2013 Catalogue</p>
  <p class="page-brand right-page">Brevik Office Supplies</p>
</section>

<section class="spread cover-spread" aria-label="Front and back cover">
  <svg width="1040" height="380" viewBox="0 0 1040 380">
    <defs>
      <linearGradient id="collage-tones" x1="0" y1="0" x2="1" y2="1">
        <stop offset="0" stop-color="#3f6fa8"/>
        <stop offset="0.35" stop-color="#8fa4b8"/>
        <stop offset="0.6" stop-color="#4d8a4a"/>
        <stop offset="0.85" stop-color="#2b2b2e"/>
        <stop offset="1" stop-color="#6b7f96"/>
      </linearGradient>
    </defs>
    <rect class="back-cover" x="0" y="0" width="490" height="380" fill="var(--yellow)"/>
    <rect class="spine" x="490" y="0" width="60" height="380" fill="var(--yellow-deep)"/>
    <rect class="front-cover" x="550" y="0" width="490" height="380" fill="var(--yellow)"/>

    <text class="cover-text" x="74" y="180"><tspan class="label">Catalogue</tspan> <tspan class="year">2013</tspan></text>
    <line x1="243" y1="148" x2="243" y2="186" stroke="#ffffff" stroke-opacity="0.7" stroke-width="1"/>
    <text class="cover-brand" x="260" y="175">Brevik Office Supplies</text>

    <g role="img" aria-label="Collage of office products: stationery, computer mice, discs, markers and cleaning supplies">
      <path d="M337,62 Q440,40 513,0 L650,0 Q600,50 608,100 Q570,170 575,340 Q480,170 337,62 Z" fill="url(#collage-tones)"/>
    </g>

    <text class="cover-brand" x="628" y="175">Brevik Office Supplies</text>
    <line x1="806" y1="148" x2="806" y2="186" stroke="#ffffff" stroke-opacity="0.7" stroke-width="1"/>
    <text class="cover-text" x="820" y="180"><tspan class="year">2013</tspan><tspan class="label" dy="-14">Catalogue</tspan></text>
  </svg>
</section>

</body>
</html>
```